real esate business card with company logo and name

we need a business card design for a real esate company

The company name is Walsh & Brand Pty Ltd, and we have our logo designed and will upload. We want classic or moden feel. Black or white background. looks more textured. Should include folowinginformations
Owen Walsh and Lucy Brand
Sales Agents & Onsite Manager
p: 07 5948 2063
F: 07 5948 2174
M:0431 857 219
3/42 Marlow Crescent, FERNLEA QLD 4213

We want this business card looks professonal. Thank you in advance.

Industry/Entity Type

Real Estate Agent

Contact Information for Business Card

Owen Walsh and Lucy Brand
Onsite Manager & Sales Agents
p: 07 5948 2063
M:0431 857 219

Font styles to use
Serif

Colors
000000
fbfbfb
333333
959595

Requirements
Must have
• company logo and name, black or white back ground

```html
<!DOCTYPE html>
<html lang="en">
<head>
<meta charset="utf-8">
<title>Walsh &amp; Brand Pty Ltd – Business Card</title>
<link href="https://fonts.googleapis.com/css2?family=Lato:wght@400;700&display=swap" rel="stylesheet">
<style>
  :root {
    --ink: #000000;
    --paper: #fbfbfb;
    --charcoal: #333333;
    --silver: #959595;
    --band: #5f5f5f;
    --logo-text: #bdbdbd;
    --backdrop: #2b2b2b;
  }
  * { margin: 0; padding: 0; box-sizing: border-box; }
  html, body { width: 1200px; height: 1086px; overflow: hidden; }
  body {
    background: var(--backdrop);
    font-family: "Lato", Arial, sans-serif;
    position: relative;
  }
  .card {
    position: absolute;
    left: 254px;
    width: 678px;
    height: 386px;
    overflow: hidden;
  }
  .card--front { top: 126px; background: var(--paper); }
  .card--back { top: 586px; background: var(--ink); }
  .card__shape { position: absolute; inset: 0; width: 100%; height: 100%; }

  .brand {
    position: absolute;
    display: flex;
    flex-direction: column;
    align-items: center;
    transform: translateX(-50%);
  }
  .brand__square {
    width: 92px;
    height: 92px;
    background: var(--band);
  }
  .brand__name {
    margin-top: 28px;
    font-weight: 400;
    font-size: 17px;
    letter-spacing: 0.5px;
    color: var(--logo-text);
    white-space: nowrap;
  }
  .card--front .brand { left: 133px; top: 130px; }
  .card--back .brand { left: 340px; top: 120px; }

  .agent {
    position: absolute;
    left: 368px;
    top: 74px;
    color: var(--ink);
  }
  .agent__name { font-weight: 700; font-size: 30px; line-height: 1.1; }
  .agent__role { font-weight: 400; font-size: 23px; line-height: 1.3; color: var(--charcoal); }

  .contacts {
    position: absolute;
    left: 363px;
    top: 160px;
    list-style: none;
    color: var(--ink);
    font-size: 20.5px;
    line-height: 25.5px;
  }
  .contacts__item { display: flex; align-items: center; }
  .contacts__icon { width: 18px; height: 18px; margin-right: 7px; flex: none; }

  .address {
    position: absolute;
    left: 363px;
    top: 261px;
    font-style: normal;
    font-size: 20.5px;
    line-height: 25px;
    color: var(--ink);
  }
</style>
</head>
<body>

<section class="card card--front" aria-label="Business card front">
  <svg class="card__shape" viewBox="0 0 847 483" preserveAspectRatio="none" aria-hidden="true">
    <path d="M0 0 H310 Q476 241 306 483 H0 Z" fill="var(--band)"/>
    <path d="M0 0 H304 Q446 241 300 483 H0 Z" fill="var(--paper)"/>
    <path d="M0 0 H300 Q442 241 296 483 H0 Z" fill="var(--ink)"/>
  </svg>

  <div class="brand">
    <div class="brand__square"></div>
    <p class="brand__name">WALSH &amp; BRAND PTY LTD.</p>
  </div>

  <div class="agent">
    <h1 class="agent__name">Owen Walsh</h1>
    <p class="agent__role">Sales Agents</p>
  </div>

  <ul class="contacts">
    <li class="contacts__item">
      <svg class="contacts__icon" viewBox="0 0 18 18" aria-label="Mobile">
        <rect x="5" y="1.5" width="8" height="15" rx="1.5" fill="none" stroke="var(--ink)" stroke-width="1.6"/>
        <rect x="7.5" y="13.5" width="3" height="1.2" fill="var(--ink)"/>
      </svg>0431 857 219
    </li>
    <li class="contacts__item">
      <svg class="contacts__icon" viewBox="0 0 18 18" aria-label="Phone">
        <path d="M1.5 7 Q9 2 16.5 7 L15 9 L12 8 L12 6.5 Q9 5.5 6 6.5 L6 8 L3 9 Z" fill="var(--ink)"/>
        <path d="M4 10 H14 L15.5 16 H2.5 Z" fill="var(--ink)"/>
        <circle cx="9" cy="12.8" r="1.6" fill="var(--paper)"/>
      </svg>07 5948 2063
    </li>
    <li class="contacts__item">
      <svg class="contacts__icon" viewBox="0 0 18 18" aria-label="Fax">
        <rect x="5" y="2" width="8" height="4" fill="var(--ink)"/>
        <rect x="1.5" y="6.5" width="15" height="7" rx="1.2" fill="var(--ink)"/>
        <rect x="5" y="11" width="8" height="5" fill="var(--paper)" stroke="var(--ink)" stroke-width="1.2"/>
      </svg>07 5948 2174
    </li>
  </ul>

  <address class="address">
    3/42 Marlow Crescent<br>
    FERNLEA QLD 4213
  </address>
</section>

<section class="card card--back" aria-label="Business card back">
  <div class="brand">
    <div class="brand__square"></div>
    <p class="brand__name">WALSH &amp; BRAND PTY LTD.</p>
  </div>
</section>

</body>
</html>
```